Retail Jewelry Business Card Design Project

We are in need of a new business card design for a retail jewelry store. This store is in the business of fine jewelry including but not specific to bridal jewelry, diamonds, designer jewelry and watches.

This store has been in business for 20 years but continues to strive for a modern professional appeal. The main colors use for this business are a royal blue, white and silver.

Target Market(s)

Target market is ages 18-50

Industry/Entity Type

Jewelry

Requirements
Must have
• Sales Person Name
Sales Person Email Address

Store Address
Store Phone
Website

Standard business card size. No odd shapes or sizes.
Nice to have
• Overall modern feel for card.

We have thought that a design with a nice feature of the logo on the back of the card would be nice but open to ideas.
Should not have
• No specific images of jewelry should be used.

```html
<!DOCTYPE html>
<html lang="en">
<head>
<meta charset="utf-8">
<title>Evan Marlowe Fine Jewelry – Business Card</title>
<link href="https://fonts.googleapis.com/css2?family=Questrial&display=swap" rel="stylesheet">
<style>
  :root {
    --royal-blue: #2e3592;
    --lavender: #7b6fb8;
    --card-white: #ffffff;
    --ink: #2a2a3a;
    --backdrop: #e9e9ec;
  }
  * { margin: 0; padding: 0; box-sizing: border-box; }
  html, body { width: 1200px; height: 750px; overflow: hidden; }
  body {
    background: var(--backdrop);
    font-family: "Questrial", sans-serif;
    position: relative;
  }
  .card {
    position: absolute;
    top: 226px;
    width: 520px;
    height: 297px;
    overflow: hidden;
    box-shadow: 0 6px 18px rgba(0,0,0,0.18);
  }
  .card-front { left: 50px; background: var(--card-white); }
  .card-back { left: 630px; background: var(--royal-blue); color: var(--card-white); }

  .front-wave { position: absolute; inset: 0; width: 100%; height: 100%; }

  .brand-name {
    position: absolute;
    left: 0; right: 0;
    text-align: center;
    font-weight: 400;
    line-height: 1.1;
  }
  .card-front .brand-name { top: 24px; color: var(--royal-blue); font-size: 42px; }
  .card-back .brand-name { top: 86px; color: var(--card-white); font-size: 46px; }
  .brand-name .brand-line { display: block; }
  .brand-name .brand-sub { display: block; font-size: 20px; letter-spacing: 4px; text-transform: uppercase; margin-top: 4px; }

  .store-address {
    position: absolute;
    top: 134px; left: 0; right: 0;
    text-align: center;
    font-size: 13px;
    line-height: 16px;
    color: var(--ink);
  }
  .staff-name {
    position: absolute;
    top: 216px; left: 0; right: 0;
    text-align: center;
    font-size: 17px;
    letter-spacing: 0.5px;
    text-transform: uppercase;
    color: var(--card-white);
  }
  .contact-row {
    position: absolute;
    top: 252px; left: 0; right: 0;
    display: flex;
    justify-content: center;
    gap: 18px;
    font-size: 12.5px;
    color: var(--card-white);
  }
  .contact-item { display: flex; align-items: center; gap: 5px; }
  .contact-icon { width: 11px; height: 11px; }

  .website {
    position: absolute;
    top: 222px; left: 0; right: 0;
    text-align: center;
    font-size: 13px;
    letter-spacing: 2px;
  }
</style>
</head>
<body>

  <section class="card card-front" aria-label="Business card front">
    <svg class="front-wave" viewBox="0 0 520 297" preserveAspectRatio="none" aria-hidden="true">
      <path d="M0 297 L0 258 C130 185 330 165 520 168 L520 297 Z" fill="var(--royal-blue)"/>
      <path d="M0 246 C125 174 330 154 520 157" fill="none" stroke="var(--lavender)" stroke-width="3"/>
    </svg>

    <h1 class="brand-name">
      <span class="brand-line">Evan Marlowe</span>
      <span class="brand-sub">Fine Jewelry</span>
    </h1>

    <p class="store-address">2280 Linden Avenue, Bayport, FL 32499</p>

    <p class="staff-name">Evan Marlowe Hartley</p>

    <div class="contact-row">
      <span class="contact-item">
        <svg class="contact-icon" viewBox="0 0 12 12" aria-hidden="true">
          <path d="M3 1 L5 3.5 L3.8 5 C4.5 6.6 5.4 7.5 7 8.2 L8.5 7 L11 9 L9.6 11 C5 10.6 1.4 7 1 2.4 Z" fill="var(--card-white)"/>
        </svg>
        555-014-2290
      </span>
      <span class="contact-item">
        <svg class="contact-icon" viewBox="0 0 12 12" aria-hidden="true">
          <rect x="1" y="2.5" width="10" height="7" rx="1" fill="var(--card-white)"/>
          <path d="M1.5 3 L6 6.5 L10.5 3" fill="none" stroke="var(--royal-blue)" stroke-width="1"/>
        </svg>
        evan@evanmarlowejewelry.com
      </span>
    </div>
  </section>

  <section class="card card-back" aria-label="Business card back">
    <h2 class="brand-name">
      <span class="brand-line">Evan Marlowe</span>
      <span class="brand-sub">Fine Jewelry</span>
    </h2>
    <p class="website">www.evanmarlowejewelry.com</p>
  </section>

</body>
</html>
```